Modern Business Card

Modern professional business card with more than just logo and demographic info. Something memorable.

We are a trendy/modern chiropractic group with an emphasis on neurology, hence the minimalist-type brain logo. We want to convey that modern and technical aspect with professionalism and the elite nature of our practice environment.

```html
<!DOCTYPE html>
<html lang="en">
<head>
<meta charset="utf-8">
<title>Cadence Chiropractic – Business Card</title>
<link rel="stylesheet" href="https://fonts.googleapis.com/css2?family=Tinos&family=Exo+2:wght@400;600&display=swap">
<style>
  :root {
    --stage: #1c1c1e;
    --card: #07080a;
    --white: #f4f4f4;
    --grey: #8a8a8c;
    --blue: #4a86d0;
    --muted: #a9abb0;
  }
  * { margin: 0; padding: 0; box-sizing: border-box; }
  html, body { width: 1200px; height: 900px; overflow: hidden; }
  body {
    background: var(--stage);
    display: flex;
    flex-direction: column;
    align-items: center;
    justify-content: center;
    gap: 40px;
  }
  .card {
    width: 700px;
    height: 400px;
    background: var(--card);
    position: relative;
    box-shadow: 0 10px 30px rgba(0,0,0,0.6);
  }
  /* Front */
  .card-front {
    display: flex;
    align-items: center;
    justify-content: center;
  }
  .brand {
    display: flex;
    align-items: center;
    gap: 18px;
  }
  .brand-mark {
    width: 56px;
    height: 56px;
    background: var(--blue);
  }
  .brand-name {
    font-family: "Tinos", serif;
    font-weight: 400;
    color: var(--white);
    line-height: 1;
  }
  .brand-name .line-1 { display: block; font-size: 52px; letter-spacing: 2px; }
  .brand-name .line-2 { display: block; font-size: 26px; letter-spacing: 1.5px; margin-top: 4px; }
  /* Back */
  .card-back {
    display: flex;
    align-items: center;
    justify-content: center;
    gap: 22px;
  }
  .person { text-align: right; }
  .person-name {
    font-family: "Tinos", serif;
    font-size: 28px;
    color: var(--grey);
    letter-spacing: 1px;
    line-height: 1.1;
  }
  .person-title {
    font-family: "Exo 2", sans-serif;
    font-size: 21px;
    color: var(--blue);
  }
  .divider {
    width: 2px;
    height: 78px;
    background: var(--white);
  }
  .contacts { list-style: none; }
  .contact {
    display: flex;
    align-items: center;
    gap: 12px;
    font-family: "Exo 2", sans-serif;
    font-size: 19px;
    color: var(--muted);
    line-height: 1.45;
    letter-spacing: 0.5px;
  }
  .contact svg { width: 20px; height: 20px; flex: none; }
  .contact .domain { color: var(--blue); font-weight: 600; }
</style>
</head>
<body>
  <section class="card card-front" aria-label="Card front">
    <div class="brand">
      <span class="brand-mark"></span>
      <span class="brand-name">
        <span class="line-1">CADENCE</span>
        <span class="line-2">CHIROPRACTIC</span>
      </span>
    </div>
  </section>

  <section class="card card-back" aria-label="Card back">
    <div class="person">
      <p class="person-name">ETHAN MARLOW</p>
      <p class="person-title">Training Specialist</p>
    </div>
    <span class="divider"></span>
    <ul class="contacts">
      <li class="contact">
        <svg viewBox="0 0 24 24" fill="none" stroke="#4a86d0" stroke-width="1.8" aria-hidden="true">
          <circle cx="12" cy="12" r="10"/>
          <path d="M8.5 7.5l2 2-1 1.5c.8 1.6 1.9 2.7 3.5 3.5l1.5-1 2 2-1.5 1.5c-3.5-.5-7.5-4.5-8-8z"/>
        </svg>
        <span>555.014.2287</span>
      </li>
      <li class="contact">
        <svg viewBox="0 0 24 24" fill="none" stroke="#4a86d0" stroke-width="1.8" aria-hidden="true">
          <rect x="2.5" y="5" width="19" height="14"/>
          <path d="M2.5 5l9.5 8 9.5-8"/>
        </svg>
        <span>e.marlow@cadencechiro.com</span>
      </li>
      <li class="contact">
        <svg viewBox="0 0 24 24" fill="none" stroke="#4a86d0" stroke-width="1.8" aria-hidden="true">
          <circle cx="12" cy="12" r="10"/>
          <ellipse cx="12" cy="12" rx="4.5" ry="10"/>
          <path d="M2 12h20M4 7h16M4 17h16"/>
        </svg>
        <span>www.<span class="domain">cadencechiro</span>.com</span>
      </li>
    </ul>
  </section>
</body>
</html>
```